International business needs business cards

Our company, DRV Ventures Inc. is in the business of supplying a range construction products with particular emphasis on CEMENT. We have developed our own brand - TORVAN SUPPLIES - with which to infiltrate the market. We are launching our brand of cement (TORVAN Type IS Cement) into the Caribbean which is unlike anything this market has ever seen. A monopoly has existed here for the past 60-odd years and the market has now opened to allow the importation of other brands and consumers are anxious and ready for change/improvement. We are very excited to be launching and want to make a great first impression. We will be conducting workshops and seminars (from government level to the hardware store owners) and we want our business card to give us the strong, confident introduction that we need.

Target Market(s)

construction; builders; engineers; home owners

Industry/Entity Type

Construction

Contact Information for Business Card

Marisol Depree
CEO
cell # 1 555 4180736
Ground floor,Lindell Plaza Suite 2734
George Town,Grand Cayman
Cayman Islands,KY1-4823
EMAIL: m.depree@drvventuresinc.example
web site drvventuresinc.example

COMPANY: skype info drv.ventures.example

second card
Yvette Brannock-Depree
CFO
CELL# 1 555 607 3941
George Town,Grand Cayman
Cayman Islands,KY1-4823
EMAIL: y.brannockdepree@drvventuresinc.example
website drvventuresinc.example

Requirements
Must have
• Business cards must display BOTH logos - DRV is the company and TORVAN is the brand.

```html
<!DOCTYPE html>
<html lang="en">
<head>
<meta charset="utf-8">
<title>DRV Ventures Inc. — Business Card</title>
<link href="https://fonts.googleapis.com/css2?family=Arimo:wght@400;700&display=swap" rel="stylesheet">
<style>
  :root {
    --bg: #e9e6e1;
    --card-black: #0d0d0d;
    --card-white: #ffffff;
    --brand-red: #8e1a1c;
    --ink: #111111;
    --text-grey: #6a6a6a;
    --mark-grey: #7b7b7b;
  }
  * { margin: 0; padding: 0; box-sizing: border-box; }
  html, body { width: 1200px; height: 950px; overflow: hidden; }
  body {
    background: var(--bg);
    font-family: "Arimo", Arial, sans-serif;
    position: relative;
  }
  .card {
    position: absolute;
    left: 220px;
    width: 760px;
    height: 434px;
    overflow: hidden;
    box-shadow: 0 6px 18px rgba(0,0,0,.25);
  }
  /* Back */
  .card-back { top: 40px; background: var(--card-black); }
  .back-mark {
    position: absolute; left: 50%; top: 92px; transform: translateX(-50%);
    display: flex; flex-direction: column; align-items: center; gap: 18px;
  }
  .back-square { width: 150px; height: 150px; background: var(--brand-red); }
  .back-name { color: #ffffff; font-size: 26px; font-weight: 700; letter-spacing: 1px; }
  .back-url {
    position: absolute; left: 0; right: 0; bottom: 58px; text-align: center;
    color: #d8d8d8; font-size: 18px; letter-spacing: 4px;
  }
  /* Front */
  .card-front { top: 496px; background: var(--card-white); }
  .corner-bar { position: absolute; right: 0; top: 0; width: 34px; height: 112px; background: var(--ink); }
  .logo-square { position: absolute; left: 358px; top: 26px; width: 92px; height: 92px; background: var(--brand-red); }
  .company-name {
    position: absolute; left: 462px; top: 30px; color: var(--ink);
    font-weight: 700; line-height: 1;
  }
  .company-name .big { display: block; font-size: 60px; letter-spacing: 1px; }
  .company-name .small { display: block; font-size: 17px; margin-top: 4px; letter-spacing: .5px; }
  .name-band {
    position: absolute; left: 0; top: 118px; width: 450px; height: 78px;
    background: var(--brand-red); color: #ffffff; padding: 14px 0 0 40px;
  }
  .person-name { font-size: 25px; font-weight: 700; }
  .person-title { font-size: 15px; margin-top: 6px; }
  .brand-mark {
    position: absolute; right: 70px; top: 150px; display: flex; align-items: center; gap: 14px;
    color: var(--mark-grey); font-size: 34px; font-weight: 700; letter-spacing: 2px;
  }
  .brand-mark .dot { width: 46px; height: 46px; border-radius: 50%; background: var(--mark-grey); }
  .address {
    position: absolute; left: 40px; top: 222px; color: var(--text-grey);
    font-size: 16px; line-height: 1.35;
  }
  .contact-list {
    position: absolute; left: 40px; top: 326px; list-style: none;
    color: var(--text-grey); font-size: 16px; line-height: 1;
  }
  .contact-list li { display: flex; align-items: center; gap: 12px; height: 26px; }
  .contact-list svg { width: 15px; height: 15px; fill: var(--brand-red); flex: none; }
</style>
</head>
<body>
  <section class="card card-back">
    <div class="back-mark">
      <div class="back-square"></div>
      <div class="back-name">DRV Ventures Inc.</div>
    </div>
    <div class="back-url">www.drvventuresinc.example</div>
  </section>

  <section class="card card-front">
    <div class="corner-bar"></div>
    <div class="logo-square"></div>
    <div class="company-name">
      <span class="big">DRV</span>
      <span class="small">VENTURES INC.</span>
    </div>
    <div class="name-band">
      <div class="person-name">Marisol Depree</div>
      <div class="person-title">CEO</div>
    </div>
    <div class="brand-mark">
      <span class="dot"></span>
      <span>TORVAN</span>
    </div>
    <div class="address">
      Ground floor<br>
      Lindell Plaza Suite 2734<br>
      George Town,Grand Cayman<br>
      Cayman Islands,KY1-4823
    </div>
    <ul class="contact-list">
      <li>
        <svg viewBox="0 0 16 16" aria-hidden="true"><path d="M4 0h8a1 1 0 0 1 1 1v14a1 1 0 0 1-1 1H4a1 1 0 0 1-1-1V1a1 1 0 0 1 1-1zm1 2v10h6V2H5zm3 11a1 1 0 1 0 0 2 1 1 0 0 0 0-2z"/></svg>
        1 555 4180736
      </li>
      <li>
        <svg viewBox="0 0 16 16" aria-hidden="true"><path d="M0 3h16v10H0V3zm1.5 1.2L8 9l6.5-4.8V4h-13v.2z"/></svg>
        m.depree@drvventuresinc.example
      </li>
      <li>
        <svg viewBox="0 0 16 16" aria-hidden="true"><circle cx="8" cy="8" r="8"/><path d="M2 8h12M8 2c-2.5 3-2.5 9 0 12M8 2c2.5 3 2.5 9 0 12" stroke="#fff" stroke-width="1.2" fill="none"/></svg>
        drvventuresinc.example
      </li>
    </ul>
  </section>
</body>
</html>
```